Online Shop Maren

We need a web design for an online shop, called "Lirvo Dune Jewels". The shop should have an extraordinary, elegant look, as shown in the Quellwick Advertising Picture in our Briefing.pdf (attached). Please have a look at our Briefing regarding website colours, background ideas, and elements to be included. The online shop is about professional jewellery design pieces, where each piece is handmade of high quality materials, also unique pieces and unique editions possible. It should attract extraordinary people and visualize that its a very individual and unique design jewellery. You can get an idea of whom it should attract by reading our target group. Colours to be used are jewellery-Velvet red, Black / anthracite, exclusive colours, silverish-white, bronze-brown and golden.

Please play around when designing with the image pictures we attach, preferably more vertical pictures, no panoramic pictures like in Brovenka Shop. Also include the BLACK logo of lirvo dune. We include the SITEMAP in the briefing and also another folder with product pictures you can use for the draft.

Regarding Functions, the store will have the SAME (technical) functions as this page:http://www.brovenka-shop.eu/ - using the "most famous" products/categories for the starting page, going into individual product pages by clicking these images and then leading to a detailed page for one product only.

Target Market(s)

Jewellery-lovers, who appreciate extraordinary things, creative economy/fashion-industries, stylists, Style consultants, outfitter, theatres, operas, production sites, Cocktail-, Dinner and Bridefashion, exclusive traditional costume stores, dancesports and tango argento dancers

Industry/Entity Type

Shop

Requirements
Must have
• Must include:
• Colours as per briefing
• Background ideas/images as per briefing/pictures sent
• Sitemap as per briefing
• Social buttons
• Logo
• Design for 3 pages: Starting page showing big images, attractive design and the 4 popular categories
• Subpage with different products of one category (i.e. bracelets)
• Detail page with one individual product only
Should not have
• no fresh, playful colours like yellow, orange, green, blue
• no cheap design, no panorama pictures

```html
<!DOCTYPE html>
<html lang="en">
<head>
<meta charset="utf-8">
<title>Lirvo Dune Jewels</title>
<link rel="stylesheet" href="https://fonts.googleapis.com/css2?family=Cinzel:wght@400&family=Great+Vibes&family=Oswald:wght@400;600&family=Source+Sans+3:wght@400;600&display=swap">
<style>
:root{
  --ink:#050505;
  --footer:#0d0d0d;
  --gold:#c8a564;
  --gold-soft:#b89a63;
  --nav:#d5b06a;
  --text:#bdb7ad;
  --white:#f4efe6;
  --line:#2a2a2a;
  --sans:"Source Sans 3",Arial,sans-serif;
}
*{margin:0;padding:0;box-sizing:border-box}
html,body{width:1112px;height:1200px;overflow:hidden;background:var(--ink)}
body{position:relative;font-family:var(--sans);color:var(--text)}
.abs{position:absolute}

/* hero */
.hero{left:0;top:0;width:1112px;height:655px;overflow:hidden}
.hero-photo{left:0;top:0;width:100%;height:100%;
  background:
   radial-gradient(ellipse 180px 320px at 665px 430px,rgba(225,205,175,.55),transparent 70%),
   linear-gradient(180deg,#1a1320 0%,#3a2c2a 30%,#5e4a36 55%,#6b5640 75%,#3a2d22 100%);}
.hero-shade{left:0;top:0;width:100%;height:100%;background:linear-gradient(90deg,rgba(20,10,30,.55),rgba(20,10,30,.05) 60%,rgba(20,10,30,.35))}

.logo{left:168px;top:56px;width:180px;text-align:center;color:var(--gold);font-weight:400}
.logo-name{font-size:28px;line-height:1;text-align:left}
.logo-sub{font-size:17px;margin-top:10px;color:var(--white)}

.top-links{top:32px;left:602px;font-size:10px;color:var(--nav);display:flex;gap:20px;align-items:center}
.top-links .sep{color:var(--nav)}
.cart{display:flex;align-items:center;gap:6px;margin-left:20px}
.main-nav{top:76px;left:404px;font-size:10px;font-weight:600;color:var(--nav);letter-spacing:.1px}
.main-nav span{position:absolute;white-space:nowrap}

.hero-title{left:122px;top:296px;font-family:"Cinzel",serif;font-size:50px;color:var(--white);letter-spacing:1px;white-space:nowrap}
.hero-script{left:190px;top:358px;font-family:"Great Vibes",cursive;font-size:44px;color:var(--white);white-space:nowrap}
.order-btn{left:272px;top:445px;width:192px;height:43px;border-radius:22px;
  background:linear-gradient(180deg,#f6f6f6,#d6d6d6 55%,#b5b5b5);
  box-shadow:0 2px 6px rgba(0,0,0,.5);
  font-family:"Cinzel",serif;font-size:19px;color:#3a3a3a;text-align:center;line-height:43px}

/* promo banners */
.promo{top:676px;width:381px;height:129px;overflow:hidden}
.promo-store{left:167px;background:linear-gradient(90deg,#0d0d10 0%,#16141a 50%,#2a2a33 100%)}
.promo-store .photo{right:0;top:0;width:170px;height:129px;background:linear-gradient(90deg,rgba(40,40,50,0),#5a4a3a 30%,#b8242c 60%,#8a6a4a)}
.store-script{left:22px;top:4px;font-family:"Great Vibes",cursive;font-size:38px;color:var(--white)}
.store-online{left:116px;top:20px;font-size:18px;color:var(--gold)}
.store-name{left:19px;top:42px;font-size:26px;color:var(--gold)}
.store-copy{left:18px;top:85px;width:230px;font-size:12px;line-height:17px;color:var(--white)}
.promo-offer{left:565px;background:linear-gradient(90deg,#8a6c34,#a98849 45%,#7d7a74 75%,#9aa0a4)}
.promo-offer .photo{right:0;top:0;width:180px;height:129px;background:linear-gradient(90deg,rgba(150,120,70,0),#6d5a48 35%,#e8e6e2 65%,#8d949a)}
.offer-a{left:28px;top:30px;font-family:"Oswald",sans-serif;font-size:17px;color:#1a1208}
.offer-b{left:49px;top:45px;font-family:"Oswald",sans-serif;font-weight:600;font-size:29px;color:var(--white);letter-spacing:.5px}
.offer-c{left:36px;top:80px;font-family:"Oswald",sans-serif;font-size:16px;color:#1a1208}

/* sections */
.section-title{top:826px;font-size:22px;color:var(--gold-soft)}
.welcome-photo{left:167px;top:869px;width:221px;height:118px;background:linear-gradient(90deg,#6a4250,#b38a86 45%,#d8d4d2 80%,#e8e8ea)}
.welcome-copy{left:169px;top:998px;width:222px;font-size:8.6px;line-height:16px;color:var(--text)}

.arrows{left:924px;top:842px;display:flex;gap:4px}

.product{top:872px;width:161px}
.product .photo{width:161px;height:118px;border:2px solid #2b2b2b}
.p1 .photo{background:radial-gradient(circle at 50% 55%,#111 30%,#444 60%,#3a3a3a)}
.p2 .photo{background:radial-gradient(circle at 50% 55%,#8a6a2c 0%,#3d444c 45%,#2e3540)}
.p3 .photo{background:radial-gradient(circle at 50% 50%,#d8d8dc 0%,#7a7a80 45%,#3a3a3e)}
.product h3{margin-top:16px;font-size:11.5px;font-weight:600;color:#a97f3d;text-transform:uppercase}
.product p{margin-top:6px;font-size:8.6px;line-height:16px;color:var(--text)}
.buy-row{margin-top:10px;display:flex;justify-content:space-between;align-items:center}
.price{font-size:17px;color:#9b8562}
.buy-btn{width:75px;height:20px;border-radius:2px;background:linear-gradient(180deg,#fafafa,#d4d4d4);font-size:9.5px;color:#333;text-align:center;line-height:20px}

/* footer */
.footer{left:0;top:1125px;width:1112px;height:75px;background:var(--footer);border-top:1px solid var(--line)}
.footer-nav{left:171px;top:21px;font-size:7.5px;color:var(--white)}
.footer-nav span{position:absolute;white-space:nowrap}
.copyright{left:171px;top:42px;font-size:7.5px;color:var(--white);white-space:nowrap}
.social{left:875px;top:27px;display:flex;gap:4px}
.social span{width:20px;height:20px;border-radius:50%;background:#4a4f58;display:block}
</style>
</head>
<body>

<header class="hero abs">
  <div class="hero-photo abs" role="img" aria-label="Woman in a long petal gown standing on old stone palace steps before a wrought iron gate"></div>
  <div class="hero-shade abs"></div>

  <div class="logo abs">
    <div class="logo-name">Lirvo Dune</div>
    <div class="logo-sub">Jewels</div>
  </div>

  <nav class="top-links abs">
    <span>My Account</span><span class="sep">|</span>
    <span>Login</span><span class="sep">|</span>
    <span>Register</span>
    <span class="cart">
      <svg width="13" height="11" viewBox="0 0 13 11" fill="none" stroke="#d5b06a" stroke-width="1.2"><path d="M0 1h2.5l1.6 6h6.5l1.6-4.5H3.2"/><circle cx="5" cy="9.5" r="1"/><circle cx="10" cy="9.5" r="1"/></svg>
      Your cart is : 0 items
    </span>
  </nav>

  <nav class="main-nav abs">
    <span style="left:0">HOME</span>
    <span style="left:78px">ONLINE SHOP</span>
    <span style="left:186px">INFO &amp; FACTS</span>
    <span style="left:304px">PARTNER</span>
    <span style="left:396px">ABOUT ME</span>
    <span style="left:496px">CONTACT</span>
  </nav>

  <h1 class="hero-title abs">Lirvo Dune Jewels</h1>
  <div class="hero-script abs">that's inherently Human</div>
  <div class="order-btn abs">Order now</div>
</header>

<section class="promo promo-store abs">
  <div class="photo abs" role="img" aria-label="Model in a red dress posing with jewellery"></div>
  <div class="store-script abs">Store</div>
  <div class="store-online abs">Shop Online</div>
  <div class="store-name abs">Lirvo Dune</div>
  <p class="store-copy abs">It is a long established fact that a reader will be distracted by the readable...</p>
</section>

<section class="promo promo-offer abs">
  <div class="photo abs" role="img" aria-label="Model in a white jacket wearing a pearl necklace"></div>
  <div class="offer-a abs">LOREM IPSUM IS</div>
  <div class="offer-b abs">10% OFFER</div>
  <div class="offer-c abs">FOR SPECIAL PRODUCTS</div>
</section>

<h2 class="section-title abs" style="left:168px;font-weight:400">Welcome to Lirvo Dune</h2>
<div class="welcome-photo abs" role="img" aria-label="Woman wearing a pearl necklace and bracelet"></div>
<p class="welcome-copy abs">It is a long established fact that a reader will be distracted by the readable content of a page when looking at its layout. The point of using Lorem Ipsum is that it has a more-or-less normal distribution of letters, as opposed to using 'Content here, content here...</p>

<h2 class="section-title abs" style="left:422px;font-weight:400">Our Products</h2>
<div class="arrows abs">
  <svg width="8" height="9" viewBox="0 0 8 9" fill="none" stroke="#bbb" stroke-width="1.3"><path d="M5.5 1 2 4.5 5.5 8"/></svg>
  <svg width="8" height="9" viewBox="0 0 8 9" fill="none" stroke="#bbb" stroke-width="1.3"><path d="M2.5 1 6 4.5 2.5 8"/></svg>
</div>

<article class="product p1 abs" style="left:424px">
  <div class="photo" role="img" aria-label="Black beaded collar necklace"></div>
  <h3>Fine Jewel Edition</h3>
  <p>It is a long established fact that a reader will be distracted by the readable...</p>
  <div class="buy-row"><span class="price">275 €</span><span class="buy-btn">Buy Now</span></div>
</article>
<article class="product p2 abs" style="left:605px">
  <div class="photo" role="img" aria-label="Gold and crystal drop necklace"></div>
  <h3>Fine Jewel Edition</h3>
  <p>It is a long established fact that a reader will be distracted by the readable...</p>
  <div class="buy-row"><span class="price">275 €</span><span class="buy-btn">Buy Now</span></div>
</article>
<article class="product p3 abs" style="left:785px">
  <div class="photo" role="img" aria-label="Silver crystal lace collar necklace"></div>
  <h3>Fine Jewel Edition</h3>
  <p>It is a long established fact that a reader will be distracted by the readable...</p>
  <div class="buy-row"><span class="price">275 €</span><span class="buy-btn">Buy Now</span></div>
</article>

<footer class="footer abs">
  <nav class="footer-nav abs">
    <span style="left:0">HOME</span><span style="left:36px">|</span>
    <span style="left:51px">ONLINE SHOP</span><span style="left:112px">|</span>
    <span style="left:127px">INFO &amp; FACTS</span><span style="left:189px">|</span>
    <span style="left:204px">PARTNER</span><span style="left:250px">|</span>
    <span style="left:265px">ABOUT ME</span><span style="left:316px">|</span>
    <span style="left:331px">CONTACT</span>
  </nav>
  <div class="copyright abs">COPYRIGHTS 2013. LIRVO DUNE. ALL RIGHTS RESERVED.</div>
  <div class="social abs" aria-label="Social links">
    <span></span><span></span><span></span>
  </div>
</footer>

</body>
</html>
```